Tech business card design

We need an amazing business card design for our new business 'Pexla' a marketing tech startup based in Sydney, Australia. We provide an online marketplace for businesses to search and buy advertising media, connect with service providers and learn more about marketing. We wish to communicate 'cool tech', reliability and professionalism and design based around our logo.

Target Market(s)

Business Owners

Contact Information for Business Card

Name
Position
Email Address
Website
Phone Number

Font styles to use
Other font styles liked:
• Avenir & Avenir Next

Colors

Designer to choose colors to be used in the design.

```html
<!DOCTYPE html>
<html lang="en">
<head>
<meta charset="utf-8">
<title>Pexla Business Card</title>
<link rel="stylesheet" href="https://fonts.googleapis.com/css2?family=Source+Sans+3:wght@400;600;700;800&display=swap">
<style>
  :root {
    --backdrop: #e3dfdf;
    --card: #ffffff;
    --card-edge: #8a8a8f;
    --navy: #10103a;
    --ink: #1a1a1a;
    --on-navy: #ffffff;
  }
  * { box-sizing: border-box; margin: 0; padding: 0; }
  html, body { width: 975px; height: 1200px; overflow: hidden; }
  body {
    background: var(--backdrop);
    font-family: "Source Sans 3", "Helvetica Neue", Arial, sans-serif;
    position: relative;
  }
  .card {
    position: absolute;
    left: 135px;
    width: 705px;
    background: var(--card);
    border: 1px solid var(--card-edge);
    border-radius: 26px;
    overflow: hidden;
  }
  .card--front { top: 162px; height: 412px; }
  .card--back { top: 689px; height: 404px; }

  .wordmark {
    position: absolute;
    left: 0; right: 0;
    text-align: center;
    font-weight: 800;
    font-size: 140px;
    line-height: 1;
    letter-spacing: -2px;
    color: var(--navy);
  }
  .card--front .wordmark { top: 16px; }
  .card--back .wordmark { top: 106px; }

  .holder {
    position: absolute;
    top: 186px; left: 0; right: 0;
    text-align: center;
  }
  .holder__name {
    font-weight: 700;
    font-size: 22px;
    color: var(--navy);
    line-height: 1.2;
  }
  .holder__role {
    font-size: 19px;
    color: var(--ink);
    line-height: 1.3;
  }

  .rule {
    position: absolute;
    left: 0; right: 0;
    height: 3px;
    background: var(--navy);
  }
  .band {
    position: absolute;
    left: 0; right: 0; bottom: 0;
    background: var(--navy);
    color: var(--on-navy);
  }
  .card--front .rule { top: 256px; }
  .card--front .band { top: 264px; }
  .card--back .rule { top: 309px; }
  .card--back .band { top: 318px; }

  .address {
    position: absolute;
    top: 51px; left: 0; right: 0;
    text-align: center;
    padding-right: 36px;
    font-size: 16.5px;
  }
  .contacts {
    position: absolute;
    top: 94px; left: 0; right: 0;
    display: flex;
    justify-content: center;
    align-items: center;
    gap: 6px;
    font-size: 17px;
    padding-left: 4px;
  }
  .contacts__item { display: flex; align-items: center; gap: 4px; }
  .contacts__item + .contacts__item { margin-left: 4px; }
  .contacts svg { display: block; }

  .site {
    position: absolute;
    top: 20px; left: 0; right: 0;
    text-align: center;
    font-size: 21px;
    letter-spacing: 2px;
  }
</style>
</head>
<body>
  <section class="card card--front">
    <div class="wordmark">pexla</div>
    <div class="holder">
      <p class="holder__name">JOHN SMITH</p>
      <p class="holder__role">Position</p>
    </div>
    <div class="rule"></div>
    <div class="band">
      <p class="address">Street name City Name Zipcode,012345</p>
      <div class="contacts">
        <span class="contacts__item">
          <svg width="19" height="19" viewBox="0 0 20 20" aria-hidden="true">
            <circle cx="10" cy="10" r="8.8" fill="none" stroke="#fff" stroke-width="1.5"/>
            <path d="M7 5.5c.6-.3 1.1 0 1.4.6l.6 1.4c.2.5 0 .9-.4 1.2l-.4.3c.4 1.2 1.2 2.1 2.4 2.6l.3-.4c.3-.4.7-.6 1.2-.4l1.4.6c.6.3.8.8.5 1.4-.5 1-1.4 1.4-2.4 1.1-2.6-.8-4.5-2.7-5.2-5.3-.3-1 .1-1.9.8-2.5z" fill="#fff"/>
          </svg>
          012-345-6789
        </span>
        <span class="contacts__item">
          <svg width="18" height="13" viewBox="0 0 18 13" aria-hidden="true">
            <rect x="0.5" y="0.5" width="17" height="12" fill="#fff"/>
            <path d="M1 1l8 6.5L17 1M1 12l6-5.5M17 12l-6-5.5" fill="none" stroke="#10103a" stroke-width="1.2"/>
          </svg>
          info@pexla.com
        </span>
        <span class="contacts__item">
          <svg width="18" height="18" viewBox="0 0 20 20" aria-hidden="true">
            <g fill="none" stroke="#fff" stroke-width="1.4">
              <circle cx="10" cy="10" r="8.5"/>
              <ellipse cx="10" cy="10" rx="3.8" ry="8.5"/>
              <path d="M1.5 10h17M3 5.5h14M3 14.5h14"/>
            </g>
          </svg>
          www.pexla.com
        </span>
      </div>
    </div>
  </section>

  <section class="card card--back">
    <div class="wordmark">pexla</div>
    <div class="rule"></div>
    <div class="band">
      <p class="site">www.pexla.com</p>
    </div>
  </section>
</body>
</html>
```